Event Website for the Audio & Visual Industry

Convene is an exhibition aimed at meeting the business needs of audio and visual professionals – the visitors are the ones that make purchase decisions when buying anything to do with AV installation, Lighting & Entertainment Technology, DJ Technologies and even Musical Instruments.

We need to rebuild our website to reflect the professional look but with a bit of creativity/flare that is associated with the industry.

Websites whose design is along the lines we're looking for:

• http:www.pelmora.com.au
• http:www.kavrin.com
• http://www.brightpanelfair.net/ (competitor expo, like the layout. Not fantastic though, but the best I’ve seen from the industry)
• http://www.tuvelo.com.au and http://www.ostrand.com.au/ (Like these brand websites, they are clean and corporate but the use of imagery allows it to have some personality)

Target Market(s)

Corporate AV End Users, Lighting Designers, Concert/Entertainment companies, Sound Engineers

Industry/Entity Type

Business

Requirements
Must have
• Refer to the current splash page – www.convene-expo.com
This is the look and feel we have developed for our brochure. We want to expand on this and create a professional corporate look and feel without alienating existing sound, light and vision sectors.

The website's focus is to register visitors to attend the show. Please include a floating 'Register Free' Call to action. Please also include floating social media buttons. For what I mean by 'floating' check out the Social media buttons on this website: http://quorvix.com/2012/02/19/tall-boat-preview/ (scroll down to see effect).

We'll like to include a Rotating Banner at the top.

Sponsor element at the bottom off the page.

Sign up form functionality

Menu to be: About the Show, What's On, Register, How to Exhibit, Blog, Contact us.

I would like to see designs for a content page as well as the homepage.

```html
<!DOCTYPE html>
<html lang="en">
<head>
<meta charset="utf-8">
<title>Convene 2012 – Sound, Light, Vision</title>
<link rel="stylesheet" href="https://fonts.googleapis.com/css2?family=Gelasio:wght@400;700&family=Open+Sans:ital,wght@0,400;0,600;0,700;1,400&display=swap">
<style>
:root{
  --bg:#f1f1f1;
  --page:#ffffff;
  --red:#e3212b;
  --red-dark:#b5141c;
  --orange:#e8501e;
  --green:#4f9a1e;
  --green-light:#6cbc2c;
  --nav:#2f3336;
  --nav-light:#4a4f53;
  --ink:#1d1d1d;
  --text:#4a4a4a;
  --muted:#777;
  --line:#dcdcdc;
  --blue:#1f6fd1;
  --blue-dark:#1553a8;
  --fb:#3b5b98;
  --tw:#4ab3e8;
  --teal:#1ba3d6;
  --serif:'Gelasio', Georgia, serif;
  --sans:'Open Sans', Arial, sans-serif;
}
*{box-sizing:border-box;margin:0;padding:0}
html,body{width:1171px;height:1200px;overflow:hidden;background:var(--bg)}
.stage{position:relative;width:1000px;height:1025px;transform:scale(1.171);transform-origin:0 0;font-family:var(--sans);color:var(--text)}
.abs{position:absolute}
.bands{position:absolute;left:0;top:0}
.page{position:absolute;left:118px;top:0;width:765px;height:1025px;background:var(--page);box-shadow:0 0 8px rgba(0,0,0,.08)}

/* header */
.brand{left:133px;top:40px;display:flex;align-items:flex-start;gap:4px;white-space:nowrap;color:var(--ink);font-family:var(--serif)}
.brand-name{font-size:40px;line-height:44px;letter-spacing:-1px}
.brand-year{font-size:9px;line-height:9px;margin-top:14px}
.head-divider{left:330px;top:18px;width:1px;height:88px;background:var(--line)}
.event-date{left:368px;top:38px;font-family:var(--serif);font-size:13px;color:var(--orange);white-space:nowrap}
.venue{left:368px;top:57px;font-family:var(--serif);font-size:12.5px;line-height:19px;color:#555;width:260px}
.signin{top:8px;height:20px;border-radius:2px;color:#fff;font-size:9px;line-height:20px;padding-left:8px;display:flex;align-items:center;gap:5px;white-space:nowrap;overflow:hidden}
.signin i{flex:none;display:inline-block;width:9px;height:9px;background:rgba(255,255,255,.85);border-radius:1px}
.signin-fb{left:627px;width:120px;background:linear-gradient(#5574b3,var(--fb))}
.signin-tw{left:755px;width:120px;background:linear-gradient(#7cd0f5,var(--tw))}
.register-cta{left:739px;top:57px;width:134px;height:33px;border-radius:4px;background:linear-gradient(#7fc63b,#3e8d14);color:#fff;font-family:var(--serif);font-size:14px;line-height:33px;text-align:center;white-space:nowrap;box-shadow:0 2px 3px rgba(0,0,0,.25)}

/* nav */
.nav-frame{left:125px;top:117px;width:751px;height:48px;background:#e6e6e6;border-radius:3px}
.nav{left:133px;top:125px;width:735px;height:33px;background:linear-gradient(var(--nav-light),var(--nav));display:flex}
.nav a{color:#fff;text-decoration:none;font-family:var(--serif);font-size:11px;text-transform:uppercase;line-height:33px;text-align:center;white-space:nowrap;border-right:1px solid #1e2123;box-shadow:1px 0 0 #5a5f63}
.nav a:last-child{border:none;box-shadow:none}

/* banner */
.hatch{background:repeating-linear-gradient(45deg,#ececec 0 2px,#f8f8f8 2px 4px)}
.banner-frame{left:125px;top:183px;width:751px;height:277px}
.tabs{left:133px;top:191px;width:236px;height:262px}
.tab{height:65.5px;display:flex;align-items:center;gap:8px;padding-left:9px;background:linear-gradient(#7c7c7c,#565656);border-bottom:1px solid #444;color:#fff;font-size:10.5px;line-height:13px;text-transform:uppercase}
.tab.active{background:linear-gradient(var(--green-light),var(--green))}
.thumb{flex:none;width:64px;height:50px;border:3px solid #fff}
.t1{background:linear-gradient(#6d6a66,#a09a92)}
.t2{background:linear-gradient(#8a1c55,#c2365d)}
.t3{background:linear-gradient(#f7a21b,#b33a08)}
.t4{background:linear-gradient(#2b5fb4,#e06b2c)}
.hero{left:369px;top:191px;width:499px;height:262px;background:linear-gradient(#dfe0e1 0%,#cfd2d4 70%,#d54040 72%,#c83434 100%)}

/* intro */
.intro-title{left:133px;top:481px;font-size:16.5px;line-height:24px;font-weight:400;color:var(--ink);text-transform:uppercase;white-space:nowrap}
.intro-photo{left:134px;top:549px;width:119px;height:119px;border-radius:50%;border:5px solid #d4d4d4;background:radial-gradient(circle at 45% 40%,#b88a6a,#5a3524)}
.intro-text{left:276px;top:554px;width:330px;font-size:11px;line-height:17px;color:var(--text)}

/* login */
.login-frame{left:671px;top:475px;width:205px;height:198px}
.login{left:677px;top:481px;width:193px;height:187px;background:#fff;border:1px solid #cfcfcf}
.login h2{height:36px;background:linear-gradient(#f5f5f5,#d8d8d8);font-family:var(--sans);font-weight:400;font-size:14px;color:#333;line-height:36px;padding-left:10px;border-bottom:1px solid #c5c5c5}
.field-label{position:absolute;left:7px;font-size:11px;color:var(--muted)}
.field{position:absolute;left:6px;width:180px;height:23px;border:1px solid #bdbdbd;box-shadow:inset 0 1px 2px rgba(0,0,0,.12)}
.login-btn{position:absolute;left:107px;top:144px;width:78px;height:28px;border-radius:3px;background:linear-gradient(#3a8ae4,var(--blue-dark));color:#fff;font-size:13px;line-height:28px;text-align:center}

/* footer */
.footer-shade{left:118px;top:712px;width:765px;height:12px;background:linear-gradient(rgba(0,0,0,.05),rgba(0,0,0,0))}
.subscribe{left:133px;top:747px;width:450px;height:45px}
.subscribe-label{position:absolute;left:9px;top:5px;font-size:10.5px;font-weight:700;color:var(--ink);line-height:13px;white-space:nowrap}
.subscribe-label span{display:block;font-weight:400;font-size:14px;color:var(--green);line-height:18px}
.email-field{position:absolute;left:178px;top:12px;width:180px;height:22px;background:#fff;border:1px solid #bbb;font-size:10px;color:#777;line-height:20px;padding-left:6px}
.subscribe-btn{position:absolute;left:367px;top:13px;width:72px;height:21px;border-radius:3px;background:linear-gradient(#ee3a3a,var(--red-dark));color:#fff;font-size:10px;line-height:21px;text-align:center}
.foot-divider{left:660px;top:730px;width:1px;height:75px;background:var(--line)}
.partner-note{left:692px;top:745px;font-size:9px;font-style:italic;color:#333}
.partner-name{left:690px;top:758px;font-size:17px;font-weight:700;color:var(--red);white-space:nowrap}
.col-title{top:812px;font-size:11.5px;color:var(--green);text-transform:uppercase}
.col-list{top:850px;list-style:none;font-size:9.5px;line-height:19px;color:#333;white-space:nowrap}
.sponsor{left:691px;top:836px;width:116px;height:58px;border:2px solid #bbb;border-radius:3px;display:flex;align-items:center;justify-content:center;gap:6px;font-size:13px;font-weight:700;color:#222}
.sponsor i{width:14px;height:14px;border-radius:50%;background:#f08a12}
.floorplan{left:670px;top:903px}
.floorplan-text{left:700px;top:916px;color:#fff;font-size:11.5px;font-weight:700;white-space:nowrap}
.footer-rule{left:126px;top:964px;width:749px;height:1px;background:var(--line)}
.legal{left:126px;top:972px;width:600px;font-size:9px;line-height:14px;color:#333}
.legal b{font-weight:700}
.social-dot{top:977px;width:24px;height:24px;border-radius:50%;background:var(--teal)}

/* floating share */
.share-bar{left:948px;top:203px;width:52px;height:257px;background:#eef0f2;border:1px solid #dde;border-radius:3px 0 0 3px}
.count{position:absolute;left:5px;width:40px;height:26px;background:#fff;border:1px solid #ccc;border-radius:2px;text-align:center;font-size:12px;line-height:25px;color:#333}
.count.big{font-weight:700;color:#1b4f82}
.share-btn{position:absolute;left:5px;width:42px;height:15px;background:linear-gradient(#fafafa,#dcdcdc);border:1px solid #c8c8c8;border-radius:2px;font-size:8px;line-height:13px;text-align:center;color:#222;white-space:nowrap;overflow:hidden}
.share-link{position:absolute;left:6px;font-size:8px;color:#2c6db3;white-space:nowrap}
</style>
</head>
<body>
<div class="stage">

  <svg class="bands" width="1000" height="1025" viewBox="0 0 1000 1025" aria-hidden="true">
    <polygon points="0,92 0,148 118,236 118,180" fill="var(--red)"/>
    <polygon points="883,805 883,860 1000,946 1000,890" fill="var(--red)"/>
  </svg>

  <div class="page"></div>

  <!-- header -->
  <div class="abs brand"><span class="brand-name">convene</span><span class="brand-year">2012</span></div>
  <div class="abs head-divider"></div>
  <div class="abs event-date">21st t-23rd AUGUST 2012</div>
  <div class="abs venue">Harbourview Convention &amp; Exhibition Centre, Wattle Quay, Australia.</div>
  <div class="abs signin signin-fb"><i></i>Sign in with Folkspace</div>
  <div class="abs signin signin-tw"><i></i>Sign in with Wavelet</div>
  <div class="abs register-cta">REGISTER NOW!</div>

  <!-- navigation -->
  <div class="abs nav-frame"></div>
  <nav class="abs nav">
    <a style="width:167px">About the Show</a>
    <a style="width:110px">What's On</a>
    <a style="width:102px">Register</a>
    <a style="width:143px">How to Exhibit</a>
    <a style="width:78px">Blog</a>
    <a style="width:135px">Contact Us</a>
  </nav>

  <!-- rotating banner -->
  <div class="abs banner-frame hatch"></div>
  <div class="abs tabs">
    <div class="tab active"><span class="thumb t1" role="img" aria-label="AV installation thumbnail"></span>AV Installation</div>
    <div class="tab"><span class="thumb t2" role="img" aria-label="Stage lighting thumbnail"></span>Lighting &amp; Entertainment Technology</div>
    <div class="tab"><span class="thumb t3" role="img" aria-label="DJ performing thumbnail"></span>DJ Technologies</div>
    <div class="tab"><span class="thumb t4" role="img" aria-label="Musician thumbnail"></span>Musical Instruments.</div>
  </div>
  <div class="abs hero" role="img" aria-label="DJ in a suit at a deck and laptop in front of a leadlight window"></div>

  <!-- intro -->
  <h1 class="abs intro-title">Australia,s largest audio visual, entertainment &amp;<br>information communications technology event</h1>
  <div class="abs intro-photo" role="img" aria-label="Visitor smiling at the exhibition"></div>
  <p class="abs intro-text">With over 500 brands on display, Convene in association with Meridia Alliance, brings together the worlds of ICT, integrating all areas including Visual, Education, Entertainment, Audio &amp; Lighting Technology, Worship, Digital Signage and Unified Communications.</p>

  <!-- login -->
  <div class="abs login-frame hatch"></div>
  <div class="abs login">
    <h2>LOGIN</h2>
    <span class="field-label" style="top:45px">Name</span>
    <span class="field" style="top:61px"></span>
    <span class="field-label" style="top:93px">Password</span>
    <span class="field" style="top:109px"></span>
    <span class="login-btn">LOGIN</span>
  </div>

  <!-- footer -->
  <div class="abs footer-shade"></div>
  <div class="abs subscribe hatch">
    <div class="subscribe-label">SUBSCRIBE<span>OUR NEWS LETTER!</span></div>
    <div class="email-field">Email Address</div>
    <div class="subscribe-btn">SUBSCRIBE</div>
  </div>
  <div class="abs foot-divider"></div>
  <div class="abs partner-note">in association with</div>
  <div class="abs partner-name">Meridia Alliance</div>

  <div class="abs col-title" style="left:133px">Quick Links</div>
  <ul class="abs col-list" style="left:133px"><li>About the Show</li><li>What's On</li><li>Register</li><li>How to Exhibit</li><li>Blog</li></ul>
  <div class="abs col-title" style="left:269px">Services</div>
  <ul class="abs col-list" style="left:269px"><li>AV installation</li><li>Lighting &amp; Entertainment Technology</li><li>DJ Technologies</li><li>Musical Instruments</li></ul>
  <div class="abs col-title" style="left:497px">Contact Us</div>
  <ul class="abs col-list" style="left:497px"><li>Level 2,</li><li>118 Kestrel Street,</li><li>Sydney, NSW 2000, Australia.</li><li>Telephone: +61 2 5550 1420.</li><li>Fax: +61 2 5550 1421.</li></ul>
  <div class="abs col-title" style="left:690px">Sponsers</div>
  <div class="abs sponsor"><i></i>Brightline</div>

  <svg class="abs floorplan" width="330" height="44" viewBox="0 0 330 44" aria-hidden="true">
    <polygon points="18,0 330,0 330,44 18,44 0,22" fill="var(--red)"/>
    <polygon points="18,0 0,22 18,44 12,22" fill="var(--red-dark)"/>
  </svg>
  <div class="abs floorplan-text">Download The Floor Plan</div>

  <div class="abs footer-rule"></div>
  <p class="abs legal"><b>STRICTLY TRADE ONLY.</b> Entry is restricted to members of the ICT, Audio Visual and Entertainment industries.<br>Persons not in these categories, including children will not be admitted at any time.<br>© 2012 Halcrest Exhibitions, Austrlia. All rights reserved.</p>
  <span class="abs social-dot" style="left:784px"></span>
  <span class="abs social-dot" style="left:817px"></span>
  <span class="abs social-dot" style="left:851px"></span>

  <!-- floating share -->
  <div class="abs share-bar">
    <span class="count" style="top:2px">1,577</span>
    <span class="share-btn" style="top:33px">Post</span>
    <span class="count" style="top:57px">16</span>
    <span class="share-btn" style="top:88px">+1</span>
    <span class="count big" style="top:114px">403</span>
    <span class="share-btn" style="top:146px">Share</span>
    <span class="share-btn" style="top:172px;font-weight:700;color:#35465c">Scrapbin</span>
    <span class="share-link" style="top:205px">✉ email</span>
    <span class="share-link" style="top:234px">↗ share</span>
  </div>

</div>
</body>
</html>
```